indépendant en tant que Massothérapeute et Préparateur Mental, j'ai besoin de ...

Massothérapeute et préparateur mental indépendant, je recherche une carte de visite sobre et dynamique, sans images liées au massage ou à la préparation mentale mais intégrant mon logo. Les couleurs que j'aime bien sont : Blanc, gris, anthracite, noir et jaune

Contact Information for Business Card

carte de préférence Horizontale
neutre qui puisse toucher le deux domaines Massothérapie et préparation mentale

Requirements
Must have
• mon projet doit intégrer au recto:
LOGO
Loïc Bardèze
078 513 26 48
info@loicbardeze.ch
et éventuellement www.loicbardeze.ch

et au verso les deux adresses:

Chemin des Ormilles 7B
1400 Yverdon-les-Bains

Route de la Gravière 9
1700 Fribourg

Should not have
• mon projet ne doit pas contenir d'image en liens avec le massage ni la préparation mentale.

```html
<!DOCTYPE html>
<html lang="fr">
<head>
<meta charset="utf-8">
<title>Loïc Bardèze – Cartes de visite</title>
<link rel="stylesheet" href="https://fonts.googleapis.com/css2?family=Montserrat:wght@500;600;700;800&family=Arimo:wght@400;700&display=swap">
<style>
  :root {
    --stage: #2b2b2b;
    --card-dark: #1c1c1c;
    --card-dark-tone: #262626;
    --card-light: #ffffff;
    --ink: #1a1a1a;
    --ink-soft: #2e2e2e;
    --logo-light: #e6e6e6;
  }
  * { margin: 0; padding: 0; box-sizing: border-box; }
  html, body { width: 1200px; height: 1015px; overflow: hidden; }
  body {
    background: var(--stage);
    display: flex;
    flex-direction: column;
    align-items: center;
    justify-content: center;
    gap: 48px;
    font-family: "Arimo", Arial, sans-serif;
  }
  .card {
    width: 690px;
    height: 420px;
    position: relative;
    overflow: hidden;
    box-shadow: 0 10px 30px rgba(0,0,0,0.45);
  }
  /* Verso */
  .card--back { background: var(--card-dark); }
  .card__pattern {
    position: absolute; inset: 0;
    background: linear-gradient(135deg, var(--card-dark-tone), var(--card-dark) 70%);
  }
  .card__back-mark {
    position: absolute;
    left: 50%; top: 50%;
    transform: translate(-50%, -50%);
    font-family: "Montserrat", sans-serif;
    font-weight: 700;
    font-size: 30px;
    color: var(--logo-light);
    letter-spacing: 0.5px;
  }
  /* Recto */
  .card--front { background: var(--card-light); color: var(--ink); }
  .brand {
    position: absolute;
    left: 44px; top: 52px;
    display: flex; align-items: center; gap: 12px;
  }
  .brand__square { width: 22px; height: 22px; background: var(--ink); }
  .brand__name {
    font-family: "Montserrat", sans-serif;
    font-weight: 700;
    font-size: 30px;
    color: var(--ink);
  }
  .brand__role {
    position: absolute;
    left: 78px; top: 94px;
    font-family: "Montserrat", sans-serif;
    font-weight: 600;
    font-size: 11px;
    letter-spacing: 0.8px;
    font-variant: small-caps;
    color: var(--ink-soft);
  }
  .contact {
    position: absolute;
    left: 380px; top: 150px;
  }
  .contact__name {
    font-family: "Montserrat", sans-serif;
    font-weight: 800;
    font-size: 24px;
    letter-spacing: 0.6px;
    margin-bottom: 16px;
  }
  .contact__line {
    display: flex; align-items: center; gap: 8px;
    font-size: 17px; line-height: 23px;
  }
  .contact__line svg { width: 14px; height: 14px; flex: none; }
  .contact__address { font-size: 17px; line-height: 21px; margin-top: 12px; }
</style>
</head>
<body>

<section class="card card--back" aria-label="Verso de la carte">
  <div class="card__pattern" role="img" aria-label="Motif répété du monogramme en noir brillant sur fond anthracite"></div>
  <div class="card__back-mark">Loïc Bardèze</div>
</section>

<section class="card card--front" aria-label="Recto de la carte">
  <div class="brand">
    <span class="brand__square"></span>
    <span class="brand__name">Loïc Bardèze</span>
  </div>
  <div class="brand__role">Massothérapeute / Préparateur Mental</div>

  <div class="contact">
    <div class="contact__name">LOÏC BARDÈZE</div>
    <div class="contact__line">
      <svg viewBox="0 0 16 16"><path fill="#1a1a1a" d="M3.6 1.5l2.3 2.8-1.3 1.6c.9 2 2.5 3.6 4.5 4.5l1.6-1.3 2.8 2.3-1.2 2.1C7.4 13.3 2.7 8.6 1.5 3.7z"/></svg>
      <span>078 513 26 48</span>
    </div>
    <div class="contact__line">
      <svg viewBox="0 0 16 16"><rect x="1" y="3" width="14" height="10" fill="#1a1a1a"/><path d="M1.5 3.5L8 9l6.5-5.5" stroke="#fff" stroke-width="1.2" fill="none"/></svg>
      <span>info@loicbardeze.ch</span>
    </div>
    <div class="contact__line">
      <svg viewBox="0 0 16 16"><circle cx="8" cy="8" r="6.5" fill="none" stroke="#1a1a1a" stroke-width="1.5"/><ellipse cx="8" cy="8" rx="2.8" ry="6.5" fill="none" stroke="#1a1a1a" stroke-width="1.2"/><path d="M1.5 8h13M2.5 5h11M2.5 11h11" stroke="#1a1a1a" stroke-width="1.1"/></svg>
      <span>www.loicbardeze.ch</span>
    </div>
    <div class="contact__address">Chemin des Ormilles 7B<br>1400 Yverdon-les-Bains</div>
    <div class="contact__address">Route de la Gravière 9<br>1700 Freiburg</div>
  </div>
</section>

</body>
</html>
```